Federal Government Proposal Development Consulting company needs a website designed and coded

I am looking for someone to design (using an existing logo, color palette, and text fonts) and code a wordpress-based website for a Proposal Development consulting company. I have full copy for all site pages and suggestions for images/ graphics and a few example design templates to go from.

One note, from a color perspective - I included a mockup of a business card to highlight a color scheme that I tend to like - if you look at the back of the business card, the blend of the grey, blue, with the neon green highlight as a separator really seems to pop. Just a thought as you are designing the page.

I would like to see 2-3 potential design layouts, and I will select one to move forward with. Then, I would like the site to be coded for WordPress (I can provide a login to my wordpress site). I would like 1 opportunity to review the coded site and make any final tweaks.

```html
<!DOCTYPE html>
<html lang="en">
<head>
<meta charset="utf-8">
<title>Inkwell Summit Consulting LLC</title>
<link rel="stylesheet" href="https://fonts.googleapis.com/css2?family=Poppins:wght@400;500;600;700;800&display=swap">
<style>
:root{
  --blue:#0b4bc8;
  --blue-deep:#0a2f8f;
  --navy:#08184a;
  --neon:#2ee6b6;
  --ink:#111;
  --grey:#555;
  --light:#f1f3f8;
  --line:#d8dbe3;
  --star:#f5a300;
  --black:#050505;
}
*{box-sizing:border-box;margin:0;padding:0}
html,body{width:1200px;height:5172px;overflow:hidden}
body{font-family:"Poppins",sans-serif;color:var(--ink);background:#fff;position:relative}
.abs{position:absolute}
h2{font-weight:700;font-size:34px;text-align:center}

/* header */
.topbar{left:400px;top:0;width:800px;height:52px;background:var(--blue);clip-path:polygon(40px 0,100% 0,100% 100%,0 100%)}
.topbar .item{position:absolute;top:12px;display:flex;align-items:center;gap:12px;color:#fff;font-size:15px}
.ic{width:30px;height:30px;border-radius:50%;background:#fff;display:flex;align-items:center;justify-content:center}
.social{position:absolute;top:10px;width:30px;height:30px;border-radius:50%;background:#fff}
.brand{left:96px;top:16px;font-size:30px;font-weight:500;color:var(--blue-deep);line-height:1}
.brand small{display:block;font-size:14px;color:var(--grey);margin-top:4px;padding-left:40px}
.nav{left:482px;top:76px;display:flex;gap:42px;font-size:15px;align-items:center}
.nav .on{color:var(--blue);font-weight:600;border-bottom:2px solid var(--blue)}
.btn{display:inline-flex;align-items:center;justify-content:center;background:var(--blue);color:#fff;font-weight:600;border-radius:3px}
.nav .btn{width:136px;height:48px;font-size:16px;margin-left:-10px}

/* hero */
.hero{left:0;top:124px;width:1200px;height:690px;background:linear-gradient(100deg,#0e2234 0%,#2c4a5e 45%,#6c8797 75%,#a8b7c0 100%)}
.hero h1{position:absolute;left:96px;top:210px;color:#fff;font-size:56px;font-weight:700}
.hero p{position:absolute;left:97px;top:290px;width:440px;color:#fff;font-size:15px;line-height:30px}
.hero .btn{position:absolute;left:97px;top:376px;width:134px;height:44px;font-size:16px}

.lead{font-size:14.5px;line-height:31px;color:#222;text-align:center}
.lead b{font-weight:500;color:var(--blue-deep)}

/* what we do */
.card{top:1078px;width:318px;height:322px;background:#fff;box-shadow:0 4px 16px rgba(0,0,0,.08);border-top:3px solid #888;border-bottom:4px solid var(--neon);padding:82px 30px 0}
.card .badge{position:absolute;left:50%;top:-40px;transform:translateX(-50%);width:80px;height:80px;border-radius:50%;background:#fff;border:3px solid #888;border-bottom-color:#fff;border-right-color:#fff;transform:translateX(-50%) rotate(-45deg);display:flex;align-items:center;justify-content:center}
.card .badge svg{transform:rotate(45deg)}
.card h3{font-size:17px;font-weight:600;margin-bottom:14px}
.card p{font-size:13.5px;line-height:31px;color:#333}
.card a{display:block;margin-top:6px;font-size:14px;font-weight:600;color:#111;text-decoration:underline}

/* who we are */
.who{left:0;top:1484px;width:1200px;height:542px;background:linear-gradient(180deg,#0a4fd0,#0a45b8 60%,#0a3fa8);color:#fff}
.who h2{margin-top:74px}
.who p{width:964px;margin:22px auto 0;font-size:14.5px;line-height:31px;text-align:center}
.outline{display:flex;align-items:center;justify-content:center;border:2px solid var(--neon);border-radius:3px;color:#fff;font-weight:600;font-size:16px}

/* services */
.svc-photo{left:0;top:2026px;width:600px;height:756px;background:linear-gradient(90deg,#b9c6d4 0%,#d9e0e8 55%,rgba(255,255,255,0) 100%)}
.tile{width:172px;height:150px;background:var(--light);border-radius:3px;display:flex;flex-direction:column;align-items:center;justify-content:flex-end;padding-bottom:22px;font-size:14px;line-height:18px;text-align:center;color:#333}
.tile svg{margin-bottom:14px}
.tile.on{background:var(--blue);color:var(--neon)}

/* sme */
.sme{top:2984px;height:298px;border-bottom:4px solid var(--neon);color:#fff;font-weight:600;font-size:16px;display:flex;align-items:flex-end;padding:0 0 36px 0;justify-content:center}
.arrow{width:24px;height:24px;border-radius:50%;border:1.5px solid #333;display:flex;align-items:center;justify-content:center}

/* contact */
.field{height:48px;background:#fff;border-radius:4px;font-size:13px;color:#555;padding:14px 18px}

/* testimonials */
.tcard{top:4166px;width:318px;height:380px;background:#fff;border:1px solid var(--line);border-radius:4px;box-shadow:0 2px 10px rgba(0,0,0,.06);text-align:center;padding-top:22px}
.avatar{width:124px;height:124px;border-radius:50%;margin:0 auto;background:linear-gradient(160deg,#c7ccd3,#6d7682)}
.tcard h4{font-size:17px;font-weight:600;margin-top:22px}
.tcard .loc{font-size:13px;color:#777;margin-top:2px}
.tcard .q{position:relative;font-size:13.5px;line-height:31px;color:#222;margin:10px 18px 0}
.tcard .q::before{content:"\201C";position:absolute;left:0;top:-12px;font-size:34px;font-weight:700}
.stars{color:var(--star);font-size:22px;letter-spacing:3px;margin-top:6px}

/* footer */
.foot{left:0;top:4800px;width:1200px;height:372px;background:var(--black);color:#fff}
.foot h5{font-size:18px;font-weight:600}
.foot .links a{display:block;color:#fff;font-size:14px;margin-top:12px;text-decoration:none}
.foot .ci{display:flex;align-items:center;gap:16px;font-size:14px;margin-top:22px}
</style>
</head>
<body>

<!-- header -->
<div class="abs brand">Inkwell Summit<small>Consulting LLC</small></div>
<div class="abs topbar">
  <div class="item" style="left:100px"><span class="ic"><svg width="14" height="14" viewBox="0 0 24 24"><path d="M6.6 10.8a15 15 0 0 0 6.6 6.6l2.2-2.2c.3-.3.7-.4 1-.2 1.1.4 2.3.6 3.6.6.6 0 1 .4 1 1V20c0 .6-.4 1-1 1A17 17 0 0 1 3 4c0-.6.4-1 1-1h3.5c.6 0 1 .4 1 1 0 1.3.2 2.5.6 3.6.1.3 0 .7-.2 1z" fill="#0b4bc8"/></svg></span>(555) 214-0387</div>
  <div class="item" style="left:318px"><span class="ic"><svg width="14" height="12" viewBox="0 0 24 18"><rect x="1" y="1" width="22" height="16" rx="2" fill="#0b4bc8"/><path d="M2 2l10 8 10-8" stroke="#fff" stroke-width="2" fill="none"/></svg></span>hello@InkwellSummit.com</div>
  <span class="social" style="left:580px"></span>
  <span class="social" style="left:622px"></span>
  <span class="social" style="left:664px"></span>
</div>
<nav class="abs nav">
  <span class="on">Home</span><span>Work with Us</span><span>Work for Us</span><span>About Us</span><span class="btn">Contact Us</span>
</nav>

<!-- hero -->
<section class="abs hero" role="img" aria-label="Engineer leaning over a robotic arm in a modern factory">
  <h1>Generate Success</h1>
  <p>Fuel Innovation in Proposal Excellence with Inkwell Summit! Click here to explore our services.</p>
  <span class="btn">Get Started</span>
</section>
<svg class="abs" style="left:0;top:640px" width="1200" height="180" viewBox="0 0 1200 180" preserveAspectRatio="none">
  <path d="M0 70 C120 40 230 120 400 110 C600 95 760 40 930 30 C1060 22 1150 60 1200 100 L1200 180 L0 180Z" fill="#0a2f8f"/>
  <path d="M0 90 C150 170 300 150 450 110 C640 60 800 30 980 40 C1090 48 1160 90 1200 120 L1200 180 L0 180Z" fill="#0b4bc8"/>
  <path d="M0 115 C160 190 320 170 480 130 C660 86 820 70 990 80 C1100 88 1170 120 1200 140 L1200 180 L0 180Z" fill="#fff"/>
</svg>

<!-- what we do -->
<h2 class="abs" style="left:0;top:876px;width:1200px">What We Do</h2>
<p class="abs lead" style="left:130px;top:938px;width:940px">Discover a dynamic approach to proposal consulting that goes beyond conventional boundaries—choose Inkwell Summit for solutions that <b>Enhance</b> the quality of your work, <b>Elevate</b> your corporate advantage, and <b>Expand</b> your industry presence.</p>

<div class="abs card" style="left:98px">
  <span class="badge"><svg width="40" height="40" viewBox="0 0 40 40" fill="none" stroke="#0a2f8f" stroke-width="2"><rect x="8" y="4" width="20" height="28"/><path d="M12 12h12M12 18h8M24 30l8-8v14H20z"/></svg></span>
  <h3>Capture Management</h3>
  <p>Elevate your business development strategy with our Capture Management services. From opportunity identification to strategic planning.</p>
  <a>Read More</a>
</div>
<div class="abs card" style="left:441px">
  <span class="badge"><svg width="40" height="40" viewBox="0 0 40 40" fill="none" stroke="#0a2f8f" stroke-width="2"><rect x="10" y="4" width="22" height="28"/><path d="M14 12h14M14 18h14M14 24h8M6 34l8-4 12 4"/></svg></span>
  <h3>Proposal Development</h3>
  <p>Transform your vision into winning proposals our Proposal Development services. We specialize in persuasive narratives,strategic pricing models.</p>
  <a>Read More</a>
</div>
<div class="abs card" style="left:784px">
  <span class="badge"><svg width="40" height="40" viewBox="0 0 40 40" fill="none" stroke="#0a2f8f" stroke-width="2"><circle cx="20" cy="18" r="10"/><path d="M16 30h8M17 34h6M20 2v4M6 8l3 3M34 8l-3 3"/><text x="14" y="22" font-size="9" font-family="Poppins,sans-serif" fill="#0a2f8f" stroke="none">AI</text></svg></span>
  <h3>Generative AI</h3>
  <p>Revolutionize your proposal writing process with our domain-aware Generative AI services. Using customer-installed tools.</p>
  <a>Read More</a>
</div>

<!-- who we are -->
<section class="abs who">
  <h2>Who We Are</h2>
  <p>Inkwell Summit, specializes in advancing an organization through a comprehensive suite of services designed to modernize the proposal development process. From innovative Capture Management strategies that pinpoint lucrative opportunities, meticulous Proposal Development services that transform concepts into effective narratives, and cutting-edge Generative AI techniques that create domain-aware content accelerating proposal draft development, we are your dedicated partner in securing success. With a unique fusion of technical expertise and exceptional writing capabilities, we surpass industry standards and set new benchmarks for excellence. Discover a dynamic approach to proposal consulting that goes beyond conventional boundaries—choose Inkwell Summit for solutions that Enhance the quality of your work, Elevate your corporate advantage, and Expand your industry presence.</p>
  <span class="abs outline" style="left:530px;top:406px;width:140px;height:50px">About Us</span>
</section>

<!-- services -->
<div class="abs svc-photo" role="img" aria-label="Consultant in a suit presenting at a whiteboard"></div>
<h2 class="abs" style="left:600px;top:2118px;width:454px">Our Services</h2>
<div class="abs" style="left:555px;top:2192px;display:grid;grid-template-columns:repeat(3,172px);gap:14px 14px">
  <div class="tile on"><svg width="52" height="48" viewBox="0 0 52 48" fill="none" stroke="#fff" stroke-width="2"><rect x="14" y="10" width="24" height="24"/><path d="M20 4v6M26 4v6M32 4v6M20 34v6M26 34v6M32 34v6M8 16h6M8 22h6M8 28h6M38 16h6M38 22h6M38 28h6"/></svg>Generative<br>AI</div>
  <div class="tile"><svg width="52" height="48" viewBox="0 0 52 48" fill="none" stroke="#0a2f8f" stroke-width="2"><circle cx="26" cy="18" r="9"/><path d="M22 30h8M10 38l10-4 12 4 10-4"/></svg>Technical<br>Solutioning</div>
  <div class="tile"><svg width="52" height="48" viewBox="0 0 52 48" fill="none" stroke="#0a2f8f" stroke-width="2"><circle cx="26" cy="18" r="11"/><path d="M20 28l-4 14 10-5 10 5-4-14"/></svg>Competitive<br>Intelligence</div>
  <div class="tile"><svg width="52" height="48" viewBox="0 0 52 48" fill="none" stroke="#0a2f8f" stroke-width="2"><rect x="12" y="4" width="24" height="32"/><circle cx="32" cy="32" r="8"/><path d="M17 12h14M17 18h10"/></svg>Proposal<br>Management</div>
  <div class="tile"><svg width="52" height="48" viewBox="0 0 52 48" fill="none" stroke="#0a2f8f" stroke-width="2"><rect x="8" y="6" width="26" height="32"/><circle cx="34" cy="28" r="8"/><path d="M40 34l6 6M13 14h16M13 20h10"/></svg>Compliance<br>Reviews</div>
  <div class="tile"><svg width="52" height="48" viewBox="0 0 52 48" fill="none" stroke="#0a2f8f" stroke-width="2"><rect x="14" y="4" width="26" height="34"/><path d="M20 30v-6M26 30v-10M32 30v-14M8 42h36"/></svg>Executive<br>Summaries</div>
  <div class="tile"><svg width="52" height="48" viewBox="0 0 52 48" fill="none" stroke="#0a2f8f" stroke-width="2"><rect x="8" y="20" width="36" height="18"/><circle cx="26" cy="11" r="6"/><path d="M14 28h24"/></svg>Past Performance<br>Writer</div>
  <div class="tile"><svg width="52" height="48" viewBox="0 0 52 48" fill="none" stroke="#0a2f8f" stroke-width="2"><path d="M26 4l4 8 9 1-7 6 2 9-8-5-8 5 2-9-7-6 9-1z"/><path d="M10 42c2-6 8-8 16-8s14 2 16 8"/></svg>Color Team<br>Reviewer</div>
  <div class="tile"><svg width="52" height="48" viewBox="0 0 52 48" fill="none" stroke="#0a2f8f" stroke-width="2"><circle cx="20" cy="10" r="5"/><circle cx="32" cy="10" r="5"/><circle cx="26" cy="20" r="5"/><path d="M6 34l10-4h14l10-6M6 42h30l10-10"/></svg>Black Hat<br>Facilitation</div>
</div>
<span class="abs btn" style="left:746px;top:2706px;width:160px;height:48px;font-size:16px">View More</span>

<!-- subject matter expertise -->
<h2 class="abs" style="left:0;top:2872px;width:1200px">Subject Matter Expertise</h2>
<div class="abs sme" style="left:98px;width:232px;background:linear-gradient(160deg,#0a1f4a,#1b4f8c)" role="img" aria-label="Glowing AI chip on a circuit board">Generative AI</div>
<div class="abs sme" style="left:330px;top:2960px;width:294px;height:362px;border:4px solid var(--neon);background:linear-gradient(160deg,#6b7f99,#4b5a70);justify-content:flex-start;padding-left:24px;font-size:19px;line-height:30px;text-align:left" role="img" aria-label="Workers on a clean-room hardware production floor">Software/ Hardware<br>Engineering</div>
<div class="abs sme" style="left:624px;width:234px;background:linear-gradient(160deg,#c99a3c,#355c84)" role="img" aria-label="Engineer in a hard hat at a control panel">Systems Engineering</div>
<div class="abs sme" style="left:858px;width:244px;background:linear-gradient(160deg,#2f5b87,#1c3350)" role="img" aria-label="Hands on a laptop with network icons">Systems Integration</div>
<span class="abs arrow" style="left:42px;top:3128px"><svg width="8" height="10" viewBox="0 0 8 10"><path d="M6 1L2 5l4 4" stroke="#333" stroke-width="1.5" fill="none"/></svg></span>
<span class="abs arrow" style="left:1134px;top:3128px"><svg width="8" height="10" viewBox="0 0 8 10"><path d="M2 1l4 4-4 4" stroke="#333" stroke-width="1.5" fill="none"/></svg></span>

<!-- contact -->
<section class="abs" style="left:0;top:3420px;width:1200px;height:560px;background:linear-gradient(180deg,#0a4fd0,#0a45b8)"></section>
<svg class="abs" style="left:0;top:3880px" width="1200" height="140" viewBox="0 0 1200 140" preserveAspectRatio="none">
  <path d="M0 0 L1200 0 L1200 30 C1080 -10 960 10 840 40 C640 90 460 110 300 100 C160 92 60 80 0 60Z" fill="#0a45b8"/>
  <path d="M0 60 C60 80 160 92 300 100 C460 110 640 90 840 40 C960 10 1080 -10 1200 30 L1200 45 C1080 10 960 30 840 60 C640 110 460 130 300 118 C160 110 60 100 0 80Z" fill="#0a2f8f"/>
</svg>
<h2 class="abs" style="left:0;top:3494px;width:1200px;color:#fff">Contact Us</h2>
<div class="abs field" style="left:182px;top:3566px;width:412px">Name</div>
<div class="abs field" style="left:606px;top:3566px;width:412px">Email</div>
<div class="abs field" style="left:182px;top:3628px;width:412px">Phone Number</div>
<div class="abs field" style="left:606px;top:3628px;width:412px">Subject</div>
<div class="abs field" style="left:182px;top:3690px;width:836px;height:86px">Message</div>
<span class="abs outline" style="left:529px;top:3798px;width:142px;height:54px;font-size:18px">Submit</span>

<!-- testimonials -->
<h2 class="abs" style="left:0;top:4086px;width:1200px">Testimonials</h2>
<div class="abs tcard" style="left:94px">
  <div class="avatar" role="img" aria-label="Client portrait"></div>
  <h4>Alex Morgan</h4><div class="loc">Florida, United States</div>
  <p class="q">Lorem ipsum dolor sit amet, consectetur adipiscing elit, sed do eiusmod tempor incididunt ut labore et aliqua.</p>
  <div class="stars">★★★★★</div>
</div>
<div class="abs tcard" style="left:438px">
  <div class="avatar" role="img" aria-label="Client portrait"></div>
  <h4>Alex Morgan</h4><div class="loc">Florida, United States</div>
  <p class="q">Lorem ipsum dolor sit amet, consectetur adipiscing elit, sed do eiusmod tempor incididunt ut labore et aliqua.</p>
  <div class="stars">★★★★★</div>
</div>
<div class="abs tcard" style="left:782px">
  <div class="avatar" role="img" aria-label="Client portrait"></div>
  <h4>Alex Morgan</h4><div class="loc">Florida, United States</div>
  <p class="q">Lorem ipsum dolor sit amet, consectetur adipiscing elit, sed do eiusmod tempor incididunt ut labore et aliqua.</p>
  <div class="stars">★★★★★</div>
</div>
<span class="abs arrow" style="left:40px;top:4344px"><svg width="8" height="10" viewBox="0 0 8 10"><path d="M6 1L2 5l4 4" stroke="#333" stroke-width="1.5" fill="none"/></svg></span>
<span class="abs arrow" style="left:1128px;top:4344px"><svg width="8" height="10" viewBox="0 0 8 10"><path d="M2 1l4 4-4 4" stroke="#333" stroke-width="1.5" fill="none"/></svg></span>

<!-- footer -->
<svg class="abs" style="left:0;top:4640px" width="1200" height="170" viewBox="0 0 1200 170" preserveAspectRatio="none">
  <path d="M0 90 C160 130 340 120 520 80 C720 36 900 10 1060 20 C1130 24 1170 34 1200 44 L1200 170 L0 170Z" fill="#0a2f8f"/>
  <path d="M0 110 C160 150 340 140 520 100 C720 56 900 34 1060 40 C1130 44 1170 54 1200 64 L1200 170 L0 170Z" fill="#0b4bc8"/>
  <path d="M0 130 C160 170 340 160 520 120 C720 76 900 56 1060 60 C1130 63 1170 72 1200 82 L1200 170 L0 170Z" fill="#050505"/>
</svg>
<footer class="abs foot">
  <div class="abs" style="left:96px;top:108px;font-size:40px;font-weight:500;line-height:1">Inkwell Summit<div style="font-size:18px;padding-left:60px;margin-top:6px;color:#ccc">Consulting LLC</div></div>
  <div class="abs links" style="left:542px;top:44px"><h5>Quick Links</h5><a>Home</a><a>Work with Us</a><a>Work for Us</a><a>About Us</a><a>Contact</a></div>
  <div class="abs" style="left:792px;top:44px"><h5>Contact Us</h5>
    <div class="ci"><span class="ic"><svg width="12" height="16" viewBox="0 0 12 16"><path d="M6 0a6 6 0 0 1 6 6c0 4-6 10-6 10S0 10 0 6a6 6 0 0 1 6-6z" fill="#0b4bc8"/><circle cx="6" cy="6" r="2" fill="#fff"/></svg></span>Inkwell Summit Consulting LLC</div>
    <div class="ci"><span class="ic"><svg width="14" height="12" viewBox="0 0 24 18"><rect x="1" y="1" width="22" height="16" rx="2" fill="#0b4bc8"/><path d="M2 2l10 8 10-8" stroke="#fff" stroke-width="2" fill="none"/></svg></span>hello@InkwellSummit.com</div>
    <div class="ci"><span class="ic"><svg width="14" height="14" viewBox="0 0 24 24"><path d="M6.6 10.8a15 15 0 0 0 6.6 6.6l2.2-2.2c.3-.3.7-.4 1-.2 1.1.4 2.3.6 3.6.6.6 0 1 .4 1 1V20c0 .6-.4 1-1 1A17 17 0 0 1 3 4c0-.6.4-1 1-1h3.5c.6 0 1 .4 1 1 0 1.3.2 2.5.6 3.6.1.3 0 .7-.2 1z" fill="#0b4bc8"/></svg></span>(555) 214-0387</div>
  </div>
  <div class="abs" style="left:98px;top:318px;width:1004px;border-top:1px solid #555"></div>
  <div class="abs" style="left:0;top:342px;width:1200px;text-align:center;font-size:13px">Copyrights@2023.Inkwell Summit Consulting LLC.All Rights Reserved</div>
</footer>

</body>
</html>
```